Alapca breeding needs a website

Presentation of the farm, animals (stallions, mares, information about the animals, for sale) and possible later expansion with a webshop (alpaca wool products). We want to present our farm and the animals on the farm on this page. A mission why we are doing this. Furthermore, each animal should be shown with a picture and described. Later we want to sell our own products made from alpaca wool via a webshop. But we still need to grow a bit to do that.

Target Market(s)

Information about my alpaca breeding and the alpaca farm

Industry/Entity Type

Tierzucht

Number of Pages Required

1 page

Font styles to use
Sans Serif

Requirements
Must have
• Modern design that matches the logo
Nice to have
• Intuitive operation / Clear structure
Should not have
• No

```html
<!DOCTYPE html>
<html lang="en">
<head>
<meta charset="utf-8">
<title>Linden Alpacas</title>
<link rel="stylesheet" href="https://fonts.googleapis.com/css2?family=Cinzel:wght@400;700;800&family=Montserrat:wght@400;500;600;700&display=swap">
<style>
:root{
  --navy:#0b2447;
  --navy-deep:#081b36;
  --green:#7cc242;
  --green-dark:#5ea52c;
  --green-pale:#e9f3dc;
  --text:#3f4650;
  --muted:#7a808a;
  --line:#d9dde2;
  --white:#ffffff;
}
*{margin:0;padding:0;box-sizing:border-box}
html,body{width:1200px;height:3728px;overflow:hidden;background:var(--white)}
body{position:relative;font-family:"Montserrat",sans-serif;color:var(--text)}
.abs{position:absolute}
.serif{font-family:"Cinzel",serif;color:var(--navy)}
.btn{position:absolute;display:flex;align-items:center;justify-content:center;background:var(--navy);color:var(--white);font:700 15px "Montserrat",sans-serif;letter-spacing:.2px;text-transform:uppercase}
.btn--green{background:var(--green)}

/* header */
.site-header{position:absolute;left:0;top:0;width:1200px;height:106px;background:var(--white);z-index:3}
.menu-icon{left:111px;top:46px}
.brand-badge{position:absolute;left:505px;top:-45px;width:190px;height:190px;border-radius:50%;background:var(--white);z-index:4;display:flex;align-items:flex-end;justify-content:center;padding-bottom:36px}
.brand-name{font:700 22px/1.05 "Cinzel",serif;color:var(--navy);text-align:center;letter-spacing:1px}
.cart{left:852px;top:40px}
.cart-count{left:870px;top:36px;font:500 11px "Montserrat",sans-serif;color:var(--navy)}
.btn--quote{left:909px;top:36px;width:179px;height:42px}

/* hero */
.hero{position:absolute;left:0;top:106px;width:1200px;height:557px;overflow:hidden}
.hero-photo{position:absolute;inset:0;background:linear-gradient(90deg,#d8c6a6 0%,#b9a07a 22%,#8f8a6e 42%,#8fa657 60%,#76b13a 78%,#5f9e2a 100%)}
.hero-title{position:absolute;left:734px;top:168px;color:var(--white);font-family:"Cinzel",serif}
.hero-title .pre{font-size:36px;font-weight:400;display:block;line-height:1}
.hero-title .big{font-size:88px;font-weight:700;display:block;line-height:1;margin-top:10px}
.hero-title .sub{font-size:56px;font-weight:400;display:block;line-height:1;margin-top:-2px}
.hero-curve{position:absolute;left:0;bottom:0}
.arrow{position:absolute}

/* about */
.about-kicker{left:113px;top:748px;font-size:40px;font-weight:400}
.about-title{left:113px;top:790px;font-size:47px;font-weight:800}
.copy{font-size:16.5px;line-height:28px;color:var(--text)}
.about-copy{left:111px;top:865px;width:500px}
.about-copy p+p{margin-top:13px}
.btn--about{left:111px;top:1078px;width:149px;height:42px}
.about-photo{left:718px;top:714px}

/* animals */
.section-title{position:absolute;left:0;width:1200px;text-align:center;font-family:"Cinzel",serif;color:var(--navy);font-size:43px;font-weight:400}
.section-title b{font-weight:800}
.animals-band{left:360px;top:1365px;width:840px;height:806px;background:var(--green-pale)}
.animal-main{left:181px;top:1407px;width:839px;height:475px;background:linear-gradient(180deg,#8fa06a 0%,#a8b37e 28%,#7d9a3e 45%,#6f9a2f 70%,#88a83c 100%)}
.animal-main::after{content:"";position:absolute;left:130px;top:90px;width:520px;height:260px;border-radius:50%;background:radial-gradient(ellipse,rgba(140,70,30,.55),rgba(140,70,30,0) 70%)}
.animal-side-left{left:0;top:1446px;width:91px;height:395px;background:linear-gradient(180deg,#6b3a1d,#a3703d 60%,#8a6538)}
.animal-side-right{left:1112px;top:1446px;width:88px;height:395px;background:linear-gradient(180deg,#9aa66d,#c9b79a 55%,#b9c47f)}
.animal-name{left:274px;top:1925px;font:700 68px/1 "Montserrat",sans-serif;color:var(--navy)}
.btn--animal{left:276px;top:2021px;width:150px;height:42px}
.animal-copy{left:698px;top:1927px;width:332px;font-size:15.5px;line-height:27.5px}

/* mission */
.mission-mark{left:-90px;top:2170px;width:440px;height:440px;border-radius:50%;background:#eef1f4}
.mission-kicker{top:2252px;font-size:40px}
.mission-title{top:2296px;font-size:46px}
.mission-copy{left:315px;top:2370px;width:570px;text-align:center}
.btn--mission{left:525px;top:2523px;width:150px;height:42px}

/* products */
.products-title{top:2665px}
.product{position:absolute;top:2776px;width:231px;height:326px;border:1px solid var(--line);background:var(--white)}
.product-img{position:absolute;left:22px;top:24px;width:187px;height:170px}
.product-name{position:absolute;left:22px;top:222px;font:500 17px "Montserrat",sans-serif;color:#444}
.product-sub{position:absolute;left:22px;top:247px;font:400 13.5px "Montserrat",sans-serif;color:var(--muted)}
.product-price{position:absolute;left:22px;top:281px;font:600 16.5px "Montserrat",sans-serif;color:var(--green)}
.btn--all{left:525px;top:3150px;width:150px;height:42px}

/* footer */
.site-footer{position:absolute;left:0;top:3245px;width:1200px;height:483px}
.footer-bg{position:absolute;inset:0}
.footer-brand{left:111px;top:3470px;width:240px;font:700 42px/1.05 "Cinzel",serif;color:var(--white);text-align:center;letter-spacing:1px}
.footer-head{font:400 17px "Cinzel",serif;color:var(--white);letter-spacing:.5px}
.footer-list{list-style:none;font:400 15.5px/28.5px "Montserrat",sans-serif;color:var(--white)}
.contact-item{position:absolute;left:456px;font:400 15.5px/28px "Montserrat",sans-serif;color:var(--white)}
.contact-item span{margin-left:28px;display:block}
.contact-item svg{position:absolute;left:0;top:6px}
.social{position:absolute;top:3576px;width:46px;height:46px;border-radius:50%;border:2px solid var(--white)}
.footer-rule{left:111px;top:3655px;width:978px;height:1px;background:rgba(255,255,255,.25)}
.copyright{left:0;top:3684px;width:1200px;text-align:center;font:400 15px "Montserrat",sans-serif;color:var(--white)}
</style>
</head>
<body>

<header class="site-header">
  <svg class="abs menu-icon" width="28" height="22" viewBox="0 0 28 22" aria-label="Menu"><path d="M0 2H28M0 11H28M0 20H28" stroke="#0b2447" stroke-width="2.6"/></svg>
  <svg class="abs cart" width="32" height="30" viewBox="0 0 32 30" aria-label="Cart"><path d="M1 3H6L10 19H26L30 8H8" fill="none" stroke="#0b2447" stroke-width="2.6" stroke-linejoin="round"/><path d="M9 9H29L26 18H11Z" fill="#0b2447"/><circle cx="12" cy="25" r="2.6" fill="#0b2447"/><circle cx="24" cy="25" r="2.6" fill="#0b2447"/></svg>
  <span class="abs cart-count">0</span>
  <a class="btn btn--quote">Request Quote</a>
</header>
<div class="brand-badge"><div class="brand-name">LINDEN<br>ALPACAS</div></div>

<section class="hero">
  <div class="hero-photo" role="img" aria-label="Photo of a young girl gently petting a fluffy cream alpaca in a green meadow"></div>
  <h1 class="hero-title"><span class="pre">WELCOME TO</span><span class="big">LINDEN</span><span class="sub">ALPACAS</span></h1>
  <svg class="arrow" style="left:40px;top:232px" width="28" height="50" viewBox="0 0 28 50"><path d="M26 2L3 25L26 48" fill="none" stroke="#fff" stroke-width="2.4"/></svg>
  <svg class="arrow" style="left:1132px;top:232px" width="28" height="50" viewBox="0 0 28 50"><path d="M2 2L25 25L2 48" fill="none" stroke="#fff" stroke-width="2.4"/></svg>
  <svg class="hero-curve" width="1200" height="120" viewBox="0 0 1200 120" preserveAspectRatio="none">
    <path d="M0 120C260 40 700 10 1200 108V120Z" fill="#7cc242"/>
    <path d="M0 120C300 70 760 48 1200 120Z" fill="#fff"/>
  </svg>
</section>

<h2 class="abs serif about-kicker">ABOUT</h2>
<h2 class="abs serif about-title">OUR FARM</h2>
<div class="abs copy about-copy">
  <p>Lorem ipsum dolor sit amet, consectetur adipiscing elit, sed do eiusmod tempor incididunt ut labore et dolore magna aliqua. Ut enim ad minim veniam, quis nostrud exercitation ullamco laboris nisi ut aliquip ex ea commodo consequat.</p>
  <p>Excepteur sint occaecat cupidatat non proident, sunt in culpa qui officia deserunt mollit anim id est laborum.</p>
</div>
<a class="btn btn--about">Read More</a>
<svg class="abs about-photo" width="370" height="440" viewBox="0 0 370 440" role="img" aria-label="Photo of a brown horse with a white blaze looking out of a wooden stable">
  <defs><linearGradient id="stableTone" x1="0" y1="0" x2="1" y2="1"><stop offset="0" stop-color="#6b4329"/><stop offset=".5" stop-color="#8a5a38"/><stop offset="1" stop-color="#c9b8a2"/></linearGradient></defs>
  <path d="M370 0C150 20 0 170 0 300V440C240 420 380 260 370 0Z" fill="url(#stableTone)"/>
</svg>

<h2 class="section-title" style="top:1232px">FARM <b>ANIMALS</b></h2>
<div class="abs animals-band"></div>
<div class="abs animal-side-left" role="img" aria-label="Photo of an animal resting on straw in a barn"></div>
<div class="abs animal-side-right" role="img" aria-label="Photo of a cream alpaca grazing on pasture"></div>
<div class="abs animal-main" role="img" aria-label="Photo of a chestnut stallion grazing in a green paddock with a white fence"></div>
<svg class="arrow" style="left:136px;top:1610px" width="26" height="48" viewBox="0 0 26 48"><path d="M24 2L3 24L24 46" fill="none" stroke="#0b2447" stroke-width="2.2"/></svg>
<svg class="arrow" style="left:1044px;top:1610px" width="26" height="48" viewBox="0 0 26 48"><path d="M2 2L23 24L2 46" fill="none" stroke="#0b2447" stroke-width="2.2"/></svg>
<h3 class="abs animal-name">Stallions</h3>
<a class="btn btn--animal">Read More</a>
<p class="abs copy animal-copy">Lorem ipsum dolor sit amet, consectetur adipiscing elit, sed do eiusmod temportor incididunt ut labore et dolore magna lorei aliqua. Quis ipsum suspendisse ultrices gravida. Risus commodo viverra maece nas accumsan lacus vel facilisis.</p>

<div class="abs mission-mark"></div>
<h2 class="section-title mission-kicker">OUR</h2>
<h2 class="section-title mission-title"><b>MISSION</b></h2>
<p class="abs copy mission-copy">Lorem ipsum dolor sit amet, consectetur adipiscing elit, sed do eiusmod tempor incididunt ut labore et dolore magna aliqua. Ut enim ad minim veniam, quis nostrud exercitation ullamco laboris nisi ut aliquip ex ea commodo consequat.</p>
<a class="btn btn--green btn--mission">Read More</a>

<h2 class="section-title products-title">ALPACA <b>WOOL PRODUCTS</b></h2>
<svg class="arrow" style="left:42px;top:2916px" width="24" height="46" viewBox="0 0 24 46"><path d="M22 2L3 23L22 44" fill="none" stroke="#b9bec5" stroke-width="2"/></svg>
<svg class="arrow" style="left:1134px;top:2916px" width="24" height="46" viewBox="0 0 24 46"><path d="M2 2L21 23L2 44" fill="none" stroke="#b9bec5" stroke-width="2"/></svg>

<article class="product" style="left:111px">
  <div class="product-img" role="img" aria-label="Photo of brown knitted wool socks" style="background:radial-gradient(ellipse at center,#6e5a48 0%,#8a7563 45%,rgba(255,255,255,0) 72%)"></div>
  <h4 class="product-name">Lorem Ipsum</h4><p class="product-sub">dolors sit amit</p><p class="product-price">$12.64</p>
</article>
<article class="product" style="left:360px">
  <div class="product-img" role="img" aria-label="Photo of a folded red plaid wool blanket" style="background:radial-gradient(ellipse at center,#c0242c 0%,#d9434a 45%,rgba(255,255,255,0) 72%)"></div>
  <h4 class="product-name">Lorem Ipsum</h4><p class="product-sub">dolors sit amit</p><p class="product-price">$10.64</p>
</article>
<article class="product" style="left:609px">
  <div class="product-img" role="img" aria-label="Photo of a blue cable knit sweater" style="background:radial-gradient(ellipse at center,#2c5aa0 0%,#3a69ad 45%,rgba(255,255,255,0) 72%)"></div>
  <h4 class="product-name">Lorem Ipsum</h4><p class="product-sub">dolors sit amit</p><p class="product-price">$12.64</p>
</article>
<article class="product" style="left:858px">
  <div class="product-img" role="img" aria-label="Photo of a mustard yellow knitted sweater" style="background:radial-gradient(ellipse at center,#e0a020 0%,#eab03a 45%,rgba(255,255,255,0) 72%)"></div>
  <h4 class="product-name">Lorem Ipsum</h4><p class="product-sub">dolors sit amit</p><p class="product-price">$10.64</p>
</article>
<a class="btn btn--all">View All</a>

<footer class="site-footer">
  <svg class="footer-bg" width="1200" height="483" viewBox="0 0 1200 483" role="img" aria-label="Dusky photo of a farm landscape with paddocks and trees, tinted dark blue">
    <defs><linearGradient id="footTone" x1="0" y1="0" x2="0" y2="1"><stop offset="0" stop-color="#12305e"/><stop offset=".55" stop-color="#0d2850"/><stop offset="1" stop-color="#0a1f40"/></linearGradient></defs>
    <path d="M0 0C400 70 800 70 1200 10V483H0Z" fill="url(#footTone)"/>
    <path d="M0 14C400 96 800 96 1200 24V60C800 110 400 110 0 50Z" fill="#1b4a8a" opacity=".55"/>
  </svg>
</footer>
<div class="abs footer-brand">LINDEN<br>ALPACAS</div>

<h5 class="abs footer-head" style="left:456px;top:3432px">CONTACT US</h5>
<div class="contact-item" style="top:3474px">
  <svg width="16" height="20" viewBox="0 0 16 20"><path d="M8 0C3.6 0 0 3.4 0 7.8 0 13 8 20 8 20S16 13 16 7.8C16 3.4 12.4 0 8 0Z" fill="#fff"/><circle cx="8" cy="7.6" r="3" fill="#0d2850"/></svg>
  <span>Linden Alpacas,<br>Address Comes Here</span>
</div>
<div class="contact-item" style="top:3538px">
  <svg width="17" height="17" viewBox="0 0 17 17"><path d="M3.5 0.5L6.5 4 5 6.3C6 8.6 8.4 11 10.7 12L13 10.5 16.5 13.5 14.8 16C8 16.5 0.5 9 1 2.2Z" fill="#fff"/></svg>
  <span>+1 555-010-0199</span>
</div>
<div class="contact-item" style="top:3573px">
  <svg width="17" height="13" viewBox="0 0 17 13"><rect width="17" height="13" rx="1.5" fill="#fff"/><path d="M1 1.5L8.5 7.5 16 1.5" fill="none" stroke="#0d2850" stroke-width="1.6"/></svg>
  <span>info@lindenalpacas.com</span>
</div>

<h5 class="abs footer-head" style="left:738px;top:3432px">QUICK LINKS</h5>
<ul class="abs footer-list" style="left:738px;top:3474px"><li>Home</li><li>About</li><li>Products</li><li>Farm Animals</li></ul>

<h5 class="abs footer-head" style="left:931px;top:3432px">OTHER LINKS</h5>
<ul class="abs footer-list" style="left:931px;top:3474px"><li>Privacy Policy</li><li>Terms &amp; Conditions</li><li>FAQs</li></ul>
<span class="social" style="left:934px" aria-label="Social profile"></span>
<span class="social" style="left:992px" aria-label="Social profile"></span>

<div class="abs footer-rule"></div>
<p class="abs copyright">2024 Linden Alpacas. All Rights Reserved.</p>

</body>
</html>
```